Banner ad design for Vorlix Display Ads

We are looking for a designer to develop a concept for banner ads for a Vorlix Display campaign we are building.

We have 3 business lines, shredding services, records management services and scanning services.

We are looking for 4 sets of ads to be created, one for each business line + one set that showcases all of our lines together.

For the design concepts, we would like to see a few sizes (banner, square, leaderboard, skyscraper, etc) for each.

The person chosen will then need to create the ads into all Vorlix supported sizes -- 20 sizes total for each set of ads as per the Vorlix size guidelines found on this page - https://help.vorlix.com/vorlix-ads/answer/5830417?hl=en&ref_topic=6402871#

A few items to note:
- Design should complement our existing brand/website look and feel (www.tamrock-dunes.ca)
- Each final ad must be 150Kb or less in size
- Final designs should be editable, meaning if we would like to change some copy in the design, we can do so using a well-known software (Canva, Photoshop/InDesign, etc)
- Some images are attached for use, but if you feel a different stock image is more suitable to to your design, please go ahead and use it.

Provided below is some messaging that can be used for each set of ads. Do not feel you need to use all of the messaging, it is provided for guidance.

SHREDDING SERVICES:

Possible Short Headline:
-- One-Time Shredding Services
-- Secure Shredding Services
-- Affordable On-Site Shredding

Possible Long Headline
-- Your Paper Can be Destroyed as Soon as the Next Business Day

Possible Descriptions:
-- TORV QQQ Certified On site shredding company. Service as soon as Next Day.
-- Secure and Affordable Toronto & GTA On-Site Shredding.
-- Certified, Affordable Office Shredding Since 2003.
-- Quick, no contact and affordable paper shredding services in Toronto & Southern Ontario.
-- Certified, Affordable Office Shredding Since 2003. Fast, no contact shredding service.

Call to Action
-- Get a Quote

RECORDS MANAGEMENT
Short Headline:
-- Off-site Records Storage
-- Records Management & Storage
-- Secure Records Storage
-- Records Management Services
-- Long Term Records Management
-- Document Storage Solutions

Possible Description
-- Local, Affordable Storage Solutions. Protect and Store your Documents in our Secure Facility
-- Local, Affordable Records Management Solutions. Store your Records in our Secure Facility
-- Certified, Affordable Document Storage Since 2004. Contact Us for a Free Quote!
-- Veltra+ Certified, Affordable Document Storage Since 2004. Contact Us for a Free Quote!

Call to Action
-- Get a Quote

SCANNING SERVICES

Short Headline:
-- Professional Scanning Company
-- Toronto & GTA Scanning Service
-- Document Scanning Services
-- Digital Conversion Services
-- Fast & Easy Retrieval

Description
-- Scan and documents and files with Professional scanning services from Tamrock-Dunes
-- Convert Your Paper Files to Electronic Files. Fast & Easy Retrieval.
-- Easily access your documents electronically with Document Scanning Services

Call to Action
-- Get a Quote

ALL SERVICES AD SET
Short Headline
-- Shred, Scan & Store Documents
-- Secure Shredding, Records Management and Scanning Services
-- #1 Document Management Company
-- Tamrock Dunes Shredding, Storage & Scanning

Description
-- Secure and Affordable Toronto & GTA On-Site Shredding, Document Storage & Scanning Company

Call to Action
-- Get a Quote

Font styles to use
Sans Serif

```html
<!DOCTYPE html>
<html lang="en">
<head>
<meta charset="utf-8">
<title>Tamrock-Dunes – Shred, Scan &amp; Store Documents</title>
<link href="https://fonts.googleapis.com/css2?family=Arimo:wght@400;500;700&display=swap" rel="stylesheet">
<style>
  :root {
    --white: #ffffff;
    --brand-navy: #1d3f66;
    --brand-accent: #2a8fd0;
    --tagline-grey: #3b3f44;
    --panel-top: #2173b6;
    --panel-bottom: #0c4d8e;
    --photo-light: #c9ccd2;
    --photo-dark: #5a6b8e;
    --desc-blue: #d2e5f6;
    --cta-green: #1fb04c;
  }
  * { margin: 0; padding: 0; box-sizing: border-box; }
  html, body {
    width: 1200px;
    height: 2400px;
    overflow: hidden;
    background: var(--white);
  }
  .ad {
    position: relative;
    width: 1200px;
    height: 2400px;
    font-family: "Arimo", Arial, sans-serif;
    overflow: hidden;
  }
  .brand-header {
    position: absolute;
    top: 0; left: 0;
    width: 1200px;
    height: 512px;
    background: var(--white);
  }
  .brand-mark {
    position: absolute;
    top: 76px;
    left: 840px;
    width: 110px;
    height: 110px;
    background: var(--brand-accent);
  }
  .brand-name {
    position: absolute;
    top: 188px;
    left: 0;
    width: 1200px;
    text-align: center;
    font-size: 104px;
    font-weight: 700;
    color: var(--brand-navy);
    letter-spacing: -2px;
    line-height: 1;
  }
  .brand-tagline {
    position: absolute;
    top: 322px;
    left: 0;
    width: 1200px;
    text-align: center;
    font-size: 70px;
    font-weight: 500;
    color: var(--tagline-grey);
    line-height: 1;
  }
  .hero-photo {
    position: absolute;
    top: 512px;
    left: 0;
    width: 1200px;
    height: 788px;
    background: linear-gradient(100deg, var(--photo-light) 0%, #a9b0bd 45%, var(--photo-dark) 100%);
  }
  .offer-panel {
    position: absolute;
    top: 1300px;
    left: 0;
    width: 1200px;
    height: 1100px;
    background: linear-gradient(180deg, var(--panel-top) 0%, var(--panel-bottom) 100%);
    text-align: center;
    color: var(--white);
  }
  .headline {
    position: absolute;
    top: 76px;
    left: 0;
    width: 1200px;
    font-size: 150px;
    font-weight: 700;
    line-height: 140px;
    text-transform: uppercase;
    letter-spacing: -1px;
  }
  .description {
    position: absolute;
    top: 540px;
    left: 90px;
    width: 1020px;
    font-size: 57px;
    font-weight: 500;
    line-height: 64px;
    color: var(--desc-blue);
  }
  .cta-button {
    position: absolute;
    top: 840px;
    left: 308px;
    width: 580px;
    height: 154px;
    background: var(--cta-green);
    color: var(--white);
    font-size: 74px;
    font-weight: 400;
    line-height: 154px;
    text-decoration: none;
    display: block;
  }
</style>
</head>
<body>
  <div class="ad">
    <header class="brand-header">
      <div class="brand-mark"></div>
      <div class="brand-name">Tamrock-Dunes</div>
      <div class="brand-tagline">Information Security</div>
    </header>

    <div class="hero-photo" role="img" aria-label="Warehouse aisle of tall blue metal shelving stacked with cardboard archive boxes"></div>

    <section class="offer-panel">
      <h1 class="headline">Shred, Scan<br>&amp; Store<br>Documents</h1>
      <p class="description">Secure and Affordable Toronto &amp; GTA On-Site Shredding, Document Storage &amp; Scanning Company</p>
      <a class="cta-button" href="#">Get a Quote</a>
    </section>
  </div>
</body>
</html>
```